Tolbek cards

I want a simple business card that pops.
Logo on one side.
On side two i want.
"Are you thinking about a new building on your property, or renovating an existing structure? Contact".....
Owners Name: Dale Whitacre
Owners Phone number: 610-555-0187
Address:4076 Copper Ridge RD, Ashmont, OH 44871
Committed to Quality, Service, and Integrity

```html
<!DOCTYPE html>
<html lang="en">
<head>
<meta charset="utf-8">
<title>Tolbek Builders LLC — Business Card</title>
<link href="https://fonts.googleapis.com/css2?family=Montserrat:wght@400;600;700&family=Playfair+Display:ital,wght@1,700&family=EB+Garamond&display=swap" rel="stylesheet">
<style>
  :root {
    --backdrop: #c8c8c8;
    --card-brown: #3f2b1c;
    --front-brown: #4a3424;
    --scene-light: #6b5038;
    --scene-dark: #35251a;
    --ink: #ffffff;
    --rule: rgba(255,255,255,0.85);
  }
  * { margin: 0; padding: 0; box-sizing: border-box; }
  html, body { width: 1200px; height: 1015px; overflow: hidden; background: var(--backdrop); }
  .sheet {
    width: 1200px; height: 1015px;
    display: flex; flex-direction: column; align-items: center; justify-content: center; gap: 50px;
  }
  .card {
    width: 700px; height: 400px; position: relative; overflow: hidden;
    box-shadow: 0 6px 18px rgba(0,0,0,0.25);
    color: var(--ink);
  }
  /* Front */
  .card-front { background: var(--front-brown); }
  .skyline {
    position: absolute; inset: 0;
    background: linear-gradient(180deg, var(--front-brown) 0%, var(--scene-light) 45%, var(--scene-dark) 60%, var(--scene-light) 75%, var(--front-brown) 100%);
    opacity: 0.9;
  }
  .brand {
    position: absolute; left: 0; right: 0; top: 50%; transform: translateY(-50%);
    display: flex; align-items: center; justify-content: center; gap: 18px;
  }
  .brand-mark { flex: none; width: 48px; height: 48px; background: var(--ink); }
  .brand-name {
    font-family: "Montserrat", sans-serif; font-weight: 700; white-space: nowrap;
    font-size: 38px; letter-spacing: 2px; color: var(--ink); text-transform: uppercase; line-height: 1;
  }
  /* Back */
  .card-back {
    background: var(--card-brown);
    display: flex; flex-direction: column; align-items: center; justify-content: center; text-align: center;
    padding: 0 50px;
  }
  .lead-in {
    font-family: "Playfair Display", serif; font-style: italic; font-weight: 700;
    font-size: 30px; line-height: 1.1;
  }
  .headline {
    font-family: "Montserrat", sans-serif; font-weight: 600;
    font-size: 23px; line-height: 1.25; letter-spacing: 0.5px; text-transform: uppercase; margin-top: 8px;
  }
  .contact-label {
    display: flex; align-items: center; width: 100%; gap: 10px; margin-top: 18px;
    font-family: "Montserrat", sans-serif; font-size: 16px; letter-spacing: 0.5px;
  }
  .contact-label .rule { flex: 1; height: 1px; background: var(--rule); position: relative; }
  .contact-label .rule::after {
    content: ""; position: absolute; top: -2px; width: 5px; height: 5px; border-radius: 50%; background: var(--ink);
  }
  .contact-label .rule-left::after { right: 0; }
  .contact-label .rule-right::after { left: 0; }
  .owner-name {
    font-family: "Montserrat", sans-serif; font-weight: 700; font-size: 24px; letter-spacing: 1px;
    text-transform: uppercase; margin-top: 12px;
  }
  .owner-phone { font-family: "Montserrat", sans-serif; font-size: 18px; letter-spacing: 1px; margin-top: 4px; }
  .short-rule { width: 50px; height: 1px; background: var(--rule); margin-top: 10px; }
  .full-rule { width: 100%; height: 1px; background: var(--rule); }
  .address { font-family: "Montserrat", sans-serif; font-size: 17px; margin: 18px 0 18px; }
  .tagline { font-family: "EB Garamond", serif; font-size: 19px; margin: 16px 0; }
</style>
</head>
<body>
<main class="sheet">
  <section class="card card-front">
    <div class="skyline" role="img" aria-label="Muted sepia photograph of a city skyline reflected in water"></div>
    <div class="brand">
      <span class="brand-mark"></span>
      <span class="brand-name">Tolbek Builders LLC</span>
    </div>
  </section>

  <section class="card card-back">
    <p class="lead-in">Are you thinking about</p>
    <h1 class="headline">A new building on your property, or<br>renovating an existing structure?</h1>
    <div class="contact-label">
      <span class="rule rule-left"></span>
      <span>Contact</span>
      <span class="rule rule-right"></span>
    </div>
    <p class="owner-name">Dale Whitacre</p>
    <p class="owner-phone">610-555-0187</p>
    <span class="short-rule"></span>
    <p class="address">4076 Copper Ridge RD, Ashmont, OH 44871</p>
    <span class="full-rule"></span>
    <p class="tagline">Committed to Quality, Service and Integrity</p>
    <span class="full-rule"></span>
  </section>
</main>
</body>
</html>
```